Letterhead Creation

I would like to create a letterhead incorporating my family crest attached. My current letterhead with my information is also attached. I would also like to add my Paralegal Rosalind Pembry

```html
<!DOCTYPE html>
<html lang="en">
<head>
<meta charset="utf-8">
<title>Letterhead – Martin Coles Esq.</title>
<link rel="stylesheet" href="https://fonts.googleapis.com/css2?family=Arimo:wght@400;700&family=Tinos:wght@400;700&display=swap">
<style>
  :root {
    --backdrop: #808080;
    --paper: #fbfbfb;
    --top-strip: #d4d4d4;
    --brand-blue: #1f409c;
    --rule-grey: #cfcfcf;
    --ink: #111111;
    --footer-text: #ffffff;
    --crest-blue: #2a4aa6;
    --crest-grey: #9a9a9a;
    --faint-crest: #efefef;
  }
  * { margin: 0; padding: 0; box-sizing: border-box; }
  html, body {
    width: 937px; height: 1200px; overflow: hidden;
    background: var(--backdrop);
  }
  .letterhead {
    position: absolute; left: 157px; top: 118px;
    width: 623px; height: 932px;
    background: var(--paper);
    overflow: hidden;
    box-shadow: 1px 2px 4px rgba(0,0,0,0.25);
  }
  .top-strip { position: absolute; left: 0; top: 0; width: 100%; height: 12px; background: var(--top-strip); }
  .sender { position: absolute; left: 51px; top: 33px; font-family: "Arimo", Arial, sans-serif; }
  .sender__paralegal { color: var(--brand-blue); font-weight: 700; font-size: 13.5px; line-height: 16px; letter-spacing: 0.2px; }
  .sender__name { margin-top: 6px; font-weight: 700; font-size: 11px; line-height: 13px; color: var(--ink); }
  .sender__address { margin-top: 1px; font-size: 11px; line-height: 13px; color: var(--ink); }
  .sender-rule { position: absolute; left: 48px; top: 103px; width: 314px; height: 2px; background: var(--rule-grey); }
  .family-crest { position: absolute; left: 427px; top: 26px; width: 150px; height: 156px; }
  .crest-backdrop { position: absolute; left: 89px; top: 266px; width: 462px; height: 504px; }
  .letter {
    position: absolute; left: 51px; top: 0; width: 517px; height: 100%;
    font-family: "Tinos", "Times New Roman", serif; font-size: 13.6px; line-height: 14.5px; color: var(--ink);
  }
  .letter p { position: absolute; left: 0; width: 517px; }
  .letter__date { top: 143px; }
  .letter__recipient { top: 313px; line-height: 15px; }
  .letter__recipient { top: 203px; }
  .letter__ref { top: 294px; font-weight: 700; }
  .letter__salutation { top: 354px; }
  .letter__body p { text-align: justify; }
  .letter__p1 { top: 386px; }
  .letter__p2 { top: 446px; }
  .letter__p3 { top: 505px; }
  .letter__closing { top: 566px; }
  sup { font-size: 8px; line-height: 0; vertical-align: 5px; }
  .contact-band {
    position: absolute; left: 0; bottom: 0; width: 100%; height: 59px;
    background: var(--brand-blue);
    display: flex; align-items: center; justify-content: center; gap: 12px;
    font-family: "Arimo", Arial, sans-serif; font-size: 12px; color: var(--footer-text);
  }
  .contact-band b { font-weight: 700; }
</style>
</head>
<body>
  <div class="letterhead">
    <div class="top-strip"></div>

    <svg class="crest-backdrop" viewBox="0 0 462 504" role="img" aria-label="Faint family crest watermark">
      <defs>
        <radialGradient id="faintTone" cx="50%" cy="55%" r="60%">
          <stop offset="0%" stop-color="#efefef"/>
          <stop offset="100%" stop-color="#fbfbfb"/>
        </radialGradient>
      </defs>
      <rect width="462" height="504" fill="url(#faintTone)"/>
    </svg>

    <header class="sender">
      <div class="sender__paralegal">PARALEGAL ROSALIND PEMBRY</div>
      <div class="sender__name">Martin Coles Esq.</div>
      <div class="sender__address">417 W. Alder Ave. Glendora, Ca 91740</div>
    </header>
    <div class="sender-rule"></div>

    <svg class="family-crest" viewBox="0 0 150 156" role="img" aria-label="Family crest">
      <defs>
        <linearGradient id="crestTone" x1="0" y1="0" x2="0" y2="1">
          <stop offset="0%" stop-color="#9a9a9a"/>
          <stop offset="100%" stop-color="#2a4aa6"/>
        </linearGradient>
      </defs>
      <rect width="150" height="156" rx="8" fill="url(#crestTone)"/>
    </svg>

    <main class="letter">
      <p class="letter__date">Issuing date: May 5, 2012</p>
      <p class="letter__recipient">Name of employee: Mr. xyz<br>Address of employee<br>address line 2</p>
      <p class="letter__ref">Ref: Promotion as an Assistant secretary</p>
      <p class="letter__salutation">Dear Mr. xyz,</p>
      <div class="letter__body">
        <p class="letter__p1">I have the pleasure to inform you that you have been promoted as assistant secretary in the share department of the company. You are required to take charge of the new assignment on 15<sup>th</sup> May, 2012. Please accept my hearty congratulations on your promotion.</p>
        <p class="letter__p2">Your salary scale in the promoted cadre will be Tk. 16,000 and from 15th may, your basic salary will be fixed at Tk. 12,000 in the said scale. You will be entitled to all other allowances as applicable to the staff-II of the company. Other services conditions remain unchanged.</p>
        <p class="letter__p3">Please acknowledge receipt of this letter.</p>
      </div>
      <p class="letter__closing">Yours sincerely,</p>
    </main>

    <footer class="contact-band">
      <span><b>Tel:</b> (626) 555-0148</span>
      <span><b>Fax:</b> (626) 555-0172</span>
      <span><b>Email:</b> Martin@colesfirmpc.com</span>
    </footer>
  </div>
</body>
</html>
```